Business Card for Coastal Tundrabridge Advisory

We need a business card for Coastal Tundrabridge Advisory. The company website address is provided below. The company logo is attached. We provide specialized permafrost services to the mining, transportation, and oil & gas industries. The card should be prepared for:
Matthias Korhonen, PhD.
Coastal Tundrabridge Advisory
PO Box 418259
Quillwater, Alaska 99642
Direct: +1-907-555-0143
Email: mkorhonen@tundrabridgeadvisory.example
Website: www.coastaltundrabridgeadvisory.example

```html
<!DOCTYPE html>
<html lang="en">
<head>
<meta charset="utf-8">
<title>Coastal Tundrabridge Advisory – Business Card</title>
<link href="https://fonts.googleapis.com/css2?family=Open+Sans:wght@300;400;600;700&display=swap" rel="stylesheet">
<style>
  :root {
    --backdrop: #222222;
    --card: #111722;
    --ink: #ffffff;
    --ink-soft: #c9ced6;
    --ghost: #1a2130;
  }
  * { margin: 0; padding: 0; box-sizing: border-box; }
  html, body { width: 1200px; height: 780px; overflow: hidden; }
  body {
    background: var(--backdrop);
    font-family: "Open Sans", Arial, sans-serif;
    color: var(--ink);
    display: flex;
    align-items: center;
    justify-content: center;
    gap: 40px;
  }
  .card {
    position: relative;
    width: 560px;
    height: 320px;
    background: var(--card);
    overflow: hidden;
    box-shadow: 0 18px 40px rgba(0,0,0,.45);
  }

  /* Back side */
  .back .brand {
    position: absolute;
    left: 0; right: 0; top: 78px;
    text-align: center;
    font-size: 36px;
    font-weight: 600;
    line-height: 1.1;
    letter-spacing: .5px;
  }
  .back .services {
    position: absolute;
    left: 0; right: 0; bottom: 52px;
    text-align: center;
  }
  .back .services-title {
    font-size: 12px;
    font-weight: 700;
    letter-spacing: .3px;
    margin-bottom: 4px;
  }
  .back .services-text {
    font-size: 11px;
    font-weight: 400;
    color: var(--ink-soft);
  }

  /* Front side */
  .front .brand {
    position: absolute;
    left: 30px; top: 28px;
    font-size: 20px;
    font-weight: 600;
    line-height: 1.15;
  }
  .front .person {
    position: absolute;
    right: 40px; top: 124px;
    text-align: right;
  }
  .front .person-name {
    font-size: 30px;
    line-height: 1.1;
  }
  .front .given { font-weight: 600; }
  .front .family { font-weight: 300; }
  .front .title {
    font-size: 17px;
    font-weight: 700;
    margin-top: 2px;
  }
  .front .accent-bar {
    position: absolute;
    right: 0; top: 160px;
    width: 18px; height: 40px;
    background: var(--ink);
  }
  .front .contact {
    position: absolute;
    left: 30px; bottom: 30px;
    font-size: 11px;
    color: var(--ink-soft);
    line-height: 1.55;
  }
  .front .address { margin-bottom: 6px; }
  .front .contact-row { display: flex; align-items: center; gap: 7px; }
  .front .contact-row svg { width: 10px; height: 10px; flex: none; }
  .front .ghost-brand {
    position: absolute;
    right: 24px; bottom: 22px;
    font-size: 28px;
    font-weight: 600;
    color: var(--ghost);
    text-align: right;
    line-height: 1.1;
  }
</style>
</head>
<body>

  <section class="card back">
    <div class="brand">Coastal Tundrabridge<br>Advisory</div>
    <div class="services">
      <p class="services-title">OUR SERVICES</p>
      <p class="services-text">We provide specialized permafrost services to the mining, transportation, and oil &amp; gas industries</p>
    </div>
  </section>

  <section class="card front">
    <div class="brand">Coastal Tundrabridge<br>Advisory</div>

    <div class="person">
      <p class="person-name"><span class="given">Matthias</span> <span class="family">Korhonen</span></p>
      <p class="title">PhD</p>
    </div>
    <div class="accent-bar"></div>

    <div class="ghost-brand">Coastal Tundrabridge<br>Advisory</div>

    <div class="contact">
      <p class="address">PO Box 418259<br>Quillwater, Alaska 99642</p>
      <p class="contact-row">
        <svg viewBox="0 0 24 24" aria-hidden="true"><path fill="#fff" d="M6.6 10.8a15.1 15.1 0 0 0 6.6 6.6l2.2-2.2a1 1 0 0 1 1-.25 11.4 11.4 0 0 0 3.6.57 1 1 0 0 1 1 1V20a1 1 0 0 1-1 1A17 17 0 0 1 3 4a1 1 0 0 1 1-1h3.5a1 1 0 0 1 1 1c0 1.25.2 2.45.57 3.57a1 1 0 0 1-.25 1z"/></svg>
        +1-907-555-0143
      </p>
      <p class="contact-row">
        <svg viewBox="0 0 24 24" aria-hidden="true"><rect x="2" y="5" width="20" height="14" rx="1" fill="none" stroke="#fff" stroke-width="2"/><path d="M2 6l10 7 10-7" fill="none" stroke="#fff" stroke-width="2"/></svg>
        mkorhonen@tundrabridgeadvisory.example
      </p>
      <p class="contact-row">
        <svg viewBox="0 0 24 24" aria-hidden="true"><circle cx="12" cy="12" r="10" fill="none" stroke="#fff" stroke-width="2"/><path d="M2 12h20M12 2c3 3 3 17 0 20M12 2c-3 3-3 17 0 20" fill="none" stroke="#fff" stroke-width="1.6"/></svg>
        www.coastaltundrabridgeadvisory.example
      </p>
    </div>
  </section>

</body>
</html>
```